New Fresh design for online Rabbit Game

Hi,

we are a french company working on a online rabbits game for kids, and not kids.

Our website is www.zorvelo.fr, but you can look at the US version : www.quintamble.com

We buy our actual design 2 years ago, but we now think it's too boring and washed out...

We need yours talent to make a really more exacting, more colorful, fresh and dynamic design.

In our game, players have to breed and train rabbits and to make them run races. Players run again friends or players.

Players are kids, between 8 and 15 years. But best players are often parents of these kids !

Our ambiance is clearly funny. We really like if color theme or background look like a nice blue sky, and / or beach. Something that make people happy to come, and say "You are here on holly days to have fun !"

I think the best is if we have 2 layouts, one for the Home page, and one for all other page.

For home page, we are really open to any proposition, we just need to keep our features :
- registration (with rabbit preview)
- connection
- game preview (images slide with small text)
- live race preview (as we have actually)

For other pages layout, we need a layout with a standard container (maybe 850 px width?), and our 2 navigation's bar.

We only need psd, no html integration.

Thanks for your help, please ask me for any questions.
Updates

Hi, 

I have just added some information, concerning layout.

Also we have just committed the budget.

Target Market(s)

Mostly kids between 8 and 15 years.

Industry/Entity Type

It Company

Requirements
Must have
• We already have some characters, like Mr Wimble at the home page and our rabbits. We want to keep all of them, so new design have to match with there style (carton).

If you create an account, you will see we have a big nav bar with 6 tabs, and a little top bar. We absolutely need them to keep a easy navigation in website.

We also need some proposition of element style, like h1, h2, h3, hr, inputs, buttons, notification bubble, etc... So we can work to improve all our pages.
Nice to have
• I think the actual website is a little to wide (about 1000px width). Maybe something like 900px - 850px is more elegant ?
In this case, we can arrange pages to deal with it.

It can be cool if major colors are stil blue and green, to match a little with actual colors. But it's no very important.
Should not have
• We don't want too big header picture (for the all pages layout). I mean, players have to focus on the content.

We don't want photo realistic style, our style is cartoon.

We don't want flash. But Js animations are ok.

```html
<!DOCTYPE html>
<html lang="fr">
<head>
<meta charset="utf-8">
<title>Zorvelo.fr – Jeu d'élevage et de course de lapins</title>
<link rel="stylesheet" href="https://fonts.googleapis.com/css2?family=Source+Sans+3:ital,wght@0,400;0,600;0,700;1,700&display=swap">
<style>
  :root {
    --sky-top: #3f9fdc;
    --sky-mid: #9fd3ef;
    --sea: #5fbfcf;
    --sand: #e9d2b5;
    --sand-dark: #c9a788;
    --green: #8ab63c;
    --green-dark: #6f9a27;
    --green-text: #7fae2e;
    --white: #ffffff;
    --ink: #2e2e2e;
    --muted: #777777;
    --panel-grey: #f3f3f3;
    --line: #cfcfcf;
    --orange: #d9731c;
    --footer-band: rgba(60, 40, 30, 0.35);
  }
  * { box-sizing: border-box; margin: 0; padding: 0; }
  html, body { width: 1200px; height: 1200px; overflow: hidden; }
  body {
    position: relative;
    font-family: "Source Sans 3", "Myriad Pro", sans-serif;
    color: var(--ink);
    background: linear-gradient(180deg,
      var(--sky-top) 0px, var(--sky-mid) 260px, #bfe6f2 330px,
      var(--sea) 420px, #6cc6cf 760px, #cfe0d6 930px,
      var(--sand) 1010px, var(--sand-dark) 1200px);
  }
  .abs { position: absolute; }

  /* Header */
  .mascot { left: 22px; top: 18px; width: 150px; height: 122px; border-radius: 50%;
    background: radial-gradient(circle, #d8cfa0 0%, #b7a874 70%, rgba(183,168,116,0) 72%); }
  .brand { left: 182px; top: 68px; font-size: 36px; font-weight: 700; color: var(--white); letter-spacing: 0.5px; }
  .grass { left: 30px; top: 134px; width: 1134px; height: 12px; border-radius: 6px;
    background: linear-gradient(180deg, #9ccc4a, #6f9a27); }

  .main-nav { left: 284px; top: 156px; height: 32px; display: flex; }
  .main-nav a { display: block; height: 32px; line-height: 32px; text-align: center;
    font-size: 20px; color: var(--ink); text-decoration: none;
    border-left: 1px solid rgba(60,60,60,0.35); }
  .main-nav a:last-child { border-right: 1px solid rgba(60,60,60,0.35); }

  /* Hero */
  .hero-band { left: 24px; top: 196px; width: 1150px; height: 296px; background: var(--green); }
  .tagline { left: 46px; top: 207px; font-size: 26px; font-weight: 700; font-style: italic; color: var(--white); }
  .hero-card { left: 36px; top: 250px; width: 1128px; height: 326px; background: var(--white); }

  .h-block { font-size: 23px; font-weight: 600; color: var(--ink); }
  .step { font-size: 19px; color: var(--green-text); }
  .field-label { font-size: 16px; color: var(--green-text); }
  .input { background: var(--white); border: 1px solid #c7c7c7; }
  .btn { display: flex; align-items: center; justify-content: center;
    font-size: 19px; font-weight: 700; color: var(--ink);
    background: linear-gradient(180deg, #c4e07c, #8ab63c); border: 1px solid #6f9a27; border-radius: 3px; }

  .signup-title { left: 66px; top: 276px; }
  .signup-step1 { left: 66px; top: 317px; }
  .rabbit-name { left: 66px; top: 344px; font-size: 19px; color: var(--ink); }
  .pencil { left: 154px; top: 344px; }
  .rabbit-preview { left: 62px; top: 436px; width: 100px; height: 100px; border-radius: 40% 40% 30% 30%;
    background: radial-gradient(circle at 50% 55%, #e87a70 0%, #d9605a 55%, rgba(255,255,255,0) 75%); }
  .picker { left: 178px; width: 106px; height: 24px; display: flex; align-items: center; justify-content: space-between;
    font-size: 16px; color: var(--ink); }
  .picker svg { display: block; }
  .picker-fur { top: 441px; }
  .picker-colour { top: 473px; }
  .picker-sex { top: 505px; }

  .signup-hint { left: 360px; top: 326px; width: 198px; text-align: right; font-size: 16px; font-weight: 600; color: var(--muted); }
  .signup-box { left: 308px; top: 355px; width: 252px; height: 191px; background: var(--panel-grey); border: 1px solid #dcdcdc; }
  .signup-step2 { left: 330px; top: 378px; }
  .signup-input { left: 325px; top: 414px; width: 216px; height: 31px; }
  .signup-step3 { left: 325px; top: 452px; }
  .signup-btn { left: 326px; top: 492px; width: 101px; height: 37px; }

  .hero-divider { left: 601px; top: 270px; width: 1px; height: 283px; background: var(--line); }
  .character { left: 630px; top: 324px; width: 198px; height: 216px; border-radius: 48% 48% 45% 45%;
    background: radial-gradient(ellipse at 50% 45%, #8c7fb8 0%, #6e6190 45%, #6a4a2e 70%, rgba(255,255,255,0) 72%); }

  .login-title { left: 864px; top: 297px; }
  .login-user-label { left: 865px; top: 344px; }
  .login-user { left: 866px; top: 367px; width: 252px; height: 31px; }
  .login-pass-label { left: 865px; top: 406px; }
  .login-pass { left: 866px; top: 434px; width: 252px; height: 31px; }
  .login-btn { left: 866px; top: 481px; width: 100px; height: 37px; }
  .forgot { left: 983px; top: 491px; font-size: 14px; color: var(--ink); }

  /* Lower panels */
  .panel { top: 600px; height: 414px; background: var(--green); }
  .panel-preview { left: 24px; width: 566px; }
  .panel-race { left: 610px; width: 566px; }
  .panel-title { top: 612px; font-size: 23px; font-weight: 600; color: var(--ink); display: flex; align-items: center; gap: 8px; }
  .preview-title { left: 46px; }
  .race-title { left: 632px; }

  .tabs { left: 108px; top: 646px; display: flex; }
  .tabs span { height: 28px; line-height: 28px; padding: 0 14px; font-size: 15px; color: #4d6e18;
    background: var(--white); border: 1px solid #c9d9a8; border-bottom: none; }
  .tabs span.is-active { background: var(--green); color: var(--white); border-color: var(--green-dark); }
  .screen { left: 46px; top: 673px; width: 518px; height: 288px; border: 3px solid #e9efdc;
    background: linear-gradient(180deg, #1fa83c 0%, #20a33b 78%, #dfe3b8 82%, #e8e6c8 100%); }
  .caption { left: 48px; top: 966px; width: 520px; font-size: 15px; line-height: 21px; color: var(--white); }
  .caption strong { color: var(--ink); font-weight: 600; }

  .race-track { left: 634px; top: 644px; width: 518px; height: 342px; border: 3px solid #e9efdc;
    background: linear-gradient(180deg, #f6ad3e 0%, #f5b54a 36%, #ffffff 36.5%, #ffffff 38%,
      #f2cd48 38.5%, #f2cd48 56%, #ffffff 56.5%, #ffffff 58%, #f0cb45 58.5%, #f0cb45 97%, #ffffff 97.5%); }

  /* Footer */
  .footer-band { left: 22px; top: 1042px; width: 1154px; height: 36px; background: var(--footer-band); border-radius: 3px; }
  .partners-label { left: 22px; top: 1042px; width: 128px; height: 36px; line-height: 36px; padding-left: 8px;
    font-size: 20px; color: var(--ink); background: rgba(255,240,220,0.75); }
  .badge { top: 1043px; height: 34px; border-radius: 3px; }
  .badge-a { left: 150px; width: 102px; background: #2a86d0; }
  .badge-b { left: 260px; width: 102px; background: #b0289a; }
  .badge-c { left: 371px; width: 103px; background: #8fd4ec; }
  .badge-d { left: 480px; width: 103px; background: #333333; border-radius: 8px; }
  .footer-links { left: 780px; top: 1050px; width: 382px; text-align: right; font-size: 14px; color: var(--white); }
  .partner-links { left: 0; top: 1090px; width: 1200px; text-align: center; font-size: 14px; color: var(--ink); }
  .partner-links b { font-weight: 400; color: var(--orange); }
</style>
</head>
<body>

  <header>
    <div class="abs mascot" role="img" aria-label="Lapin de la mascotte Zorvelo assis dans l'herbe"></div>
    <div class="abs brand">Zorvelo.fr</div>
    <div class="abs grass" role="img" aria-label="Bande d'herbe avec marguerites"></div>
    <nav class="abs main-nav">
      <a href="#" style="width:132px">Accueil</a>
      <a href="#" style="width:119px">News</a>
      <a href="#" style="width:134px">Forum</a>
      <a href="#" style="width:146px">Records</a>
      <a href="#" style="width:102px">Aide</a>
    </nav>
  </header>

  <section class="hero">
    <div class="abs hero-band"></div>
    <h1 class="abs tagline">Le plus cool des jeux d'élevages et de course de lapins !</h1>
    <div class="abs hero-card"></div>

    <h2 class="abs h-block signup-title">Nouveau joueur</h2>
    <div class="abs step signup-step1">1 - Choisissez votre lapin</div>
    <div class="abs rabbit-name">Smoking</div>
    <svg class="abs pencil" width="26" height="22" viewBox="0 0 26 22" aria-hidden="true">
      <path d="M3 19 L6 12 L19 2 L24 7 L11 17 Z" fill="#3f5f9e"/>
      <path d="M3 19 L6 12 L11 17 Z" fill="#cfd8ea"/>
    </svg>
    <div class="abs rabbit-preview" role="img" aria-label="Aperçu du lapin choisi, angora rouge"></div>

    <div class="abs picker picker-fur">
      <svg width="16" height="18" viewBox="0 0 16 18"><path d="M15 1 L2 9 L15 17 Z" fill="#7bb23a"/></svg>
      <span>Angora</span>
      <svg width="16" height="18" viewBox="0 0 16 18"><path d="M1 1 L14 9 L1 17 Z" fill="#7bb23a"/></svg>
    </div>
    <div class="abs picker picker-colour">
      <svg width="16" height="18" viewBox="0 0 16 18"><path d="M15 1 L2 9 L15 17 Z" fill="#7bb23a"/></svg>
      <span>Rouge</span>
      <svg width="16" height="18" viewBox="0 0 16 18"><path d="M1 1 L14 9 L1 17 Z" fill="#7bb23a"/></svg>
    </div>
    <div class="abs picker picker-sex">
      <svg width="16" height="18" viewBox="0 0 16 18"><path d="M15 1 L2 9 L15 17 Z" fill="#7bb23a"/></svg>
      <span>Femelle</span>
      <svg width="16" height="18" viewBox="0 0 16 18"><path d="M1 1 L14 9 L1 17 Z" fill="#7bb23a"/></svg>
    </div>

    <div class="abs signup-hint">Inscription en 3 secondes !</div>
    <div class="abs signup-box"></div>
    <div class="abs step signup-step2">2 - Choisissez un pseudo</div>
    <div class="abs input signup-input"></div>
    <div class="abs step signup-step3">3 - C'est parti</div>
    <div class="abs btn signup-btn">Jouer!</div>

    <div class="abs hero-divider"></div>
    <div class="abs character" role="img" aria-label="Mr Wimble, personnage savant préparant des légumes"></div>

    <h2 class="abs h-block login-title">Connexion</h2>
    <div class="abs field-label login-user-label">Pseudo :</div>
    <div class="abs input login-user"></div>
    <div class="abs field-label login-pass-label">Mot de passe :</div>
    <div class="abs input login-pass"></div>
    <div class="abs btn login-btn">Jouer!</div>
    <div class="abs forgot">Mot de passe oublié ?</div>
  </section>

  <section class="game-preview">
    <div class="abs panel panel-preview"></div>
    <h2 class="abs panel-title preview-title">
      <svg width="26" height="20" viewBox="0 0 26 20" aria-hidden="true">
        <circle cx="7" cy="13" r="6" fill="#3a3a3a"/><circle cx="19" cy="13" r="6" fill="#3a3a3a"/>
        <rect x="4" y="2" width="6" height="8" fill="#3a3a3a"/><rect x="16" y="2" width="6" height="8" fill="#3a3a3a"/>
        <rect x="10" y="6" width="6" height="4" fill="#3a3a3a"/>
      </svg>
      Aperçu du jeu
    </h2>
    <div class="abs tabs">
      <span class="is-active">Votre parc</span>
      <span>Votre jardin</span>
      <span>Les métiers</span>
      <span>L'univers</span>
    </div>
    <div class="abs screen" role="img" aria-label="Capture du jeu : lapins dans un parc d'herbe avec barre d'entraînement"></div>
    <p class="abs caption">Élevez, éduquez et entrainez vos lapins dans votre parc. Regardez les jouer et grandir <strong>sous vos yeux !</strong></p>
  </section>

  <section class="race-preview">
    <div class="abs panel panel-race"></div>
    <h2 class="abs panel-title race-title">Participez aux courses avec d'autres joueurs</h2>
    <div class="abs race-track" role="img" aria-label="Course en direct : lapins sur des pistes de sable"></div>
  </section>

  <footer>
    <div class="abs footer-band"></div>
    <div class="abs partners-label">Partenaires :</div>
    <div class="abs badge badge-a"></div>
    <div class="abs badge badge-b"></div>
    <div class="abs badge badge-c"></div>
    <div class="abs badge badge-d"></div>
    <div class="abs footer-links">Règlement - CGU - Contact - Zorvelo.fr 3.0</div>
    <p class="abs partner-links"><b>Partenaires :</b> Jeux - Jeux de course - Jeux d'élevage - Jeu gratuit du net - Jeu en ligne - Jeux en ligne - jeux gratuits - voir tous</p>
  </footer>

</body>
</html>
```